Business card design

Hi,
I need to have a business card design based on the current logo.
If competitive I not put it out to everyone.

It can be single of double sided

Target Market(s)

Food businesses

Industry/Entity Type

Food Manufacturing

Contact Information for Business Card

Details will on card will be as follows Name = Marcus Bell Email = Marcus@PanHearth.com.au Phone = 0418563207 Address = 57 Larkin Street , Marlow Heights QLD 4127 Australia

Font styles to use
Other font styles liked:
• based on two fonts - Adelle & Museo

Requirements
Must have
• Based on the on switch concept

```html
<!DOCTYPE html>
<html lang="en">
<head>
<meta charset="utf-8">
<title>PanHearth Business Card</title>
<link href="https://fonts.googleapis.com/css2?family=Montserrat:wght@500;600&family=Roboto:wght@400;500&family=Zilla+Slab:wght@400&display=swap" rel="stylesheet">
<style>
  :root {
    --page-bg: #1b1b1b;
    --card-bg: #0c0c0c;
    --card-edge: #202020;
    --accent: #e8264a;
    --text-light: #e6e6e6;
    --text-muted: #c9c9c9;
    --logo-grey: #c4c4c4;
    --tagline-grey: #8a8a8a;
    --divider: #3a3a3a;
  }
  * { margin: 0; padding: 0; box-sizing: border-box; }
  html, body {
    width: 1200px;
    height: 900px;
    overflow: hidden;
    background: var(--page-bg);
  }
  .sheet {
    width: 1200px;
    height: 900px;
    display: flex;
    flex-direction: column;
    align-items: center;
    justify-content: center;
    gap: 56px;
  }
  .card {
    width: 600px;
    height: 343px;
    background: var(--card-bg);
    border: 1px solid var(--card-edge);
    border-radius: 22px;
    position: relative;
    overflow: hidden;
  }

  /* Front */
  .card-front { display: flex; }
  .front-brand {
    width: 276px;
    display: flex;
    align-items: center;
    justify-content: center;
    gap: 10px;
    padding-top: 40px;
  }
  .brand-dot {
    width: 24px;
    height: 24px;
    border-radius: 50%;
    background: var(--accent);
    flex: none;
  }
  .brand-name {
    font-family: "Montserrat", sans-serif;
    font-weight: 600;
    font-size: 28px;
    letter-spacing: 0.5px;
    color: #ffffff;
    white-space: nowrap;
  }
  .front-divider {
    width: 1px;
    margin: 70px 0;
    background: var(--divider);
  }
  .front-details {
    flex: 1;
    padding: 78px 0 0 32px;
    font-family: "Roboto", Arial, sans-serif;
  }
  .person-name {
    font-weight: 500;
    font-size: 22px;
    letter-spacing: 0.5px;
    color: var(--accent);
    text-transform: uppercase;
    margin-bottom: 8px;
  }
  .address {
    font-size: 14px;
    line-height: 1.35;
    color: var(--text-muted);
    margin-bottom: 22px;
  }
  .contact-list { list-style: none; }
  .contact-item {
    display: flex;
    align-items: center;
    gap: 9px;
    font-size: 14.5px;
    line-height: 1.5;
    color: var(--text-light);
  }
  .contact-icon { width: 13px; height: 13px; flex: none; }
  .highlight { color: var(--accent); }

  /* Back */
  .card-back {
    display: flex;
    align-items: center;
    justify-content: center;
  }
  .back-lockup {
    display: flex;
    flex-direction: column;
    align-items: flex-end;
  }
  .back-mark {
    display: flex;
    align-items: center;
    gap: 14px;
  }
  .back-mark .brand-dot {
    width: 30px;
    height: 30px;
    background: var(--logo-grey);
  }
  .back-mark .brand-name {
    font-size: 38px;
    color: var(--logo-grey);
  }
  .tagline {
    margin-top: 2px;
    font-family: "Zilla Slab", Georgia, serif;
    font-size: 15px;
    color: var(--tagline-grey);
  }
</style>
</head>
<body>
<main class="sheet">

  <section class="card card-front">
    <div class="front-brand">
      <span class="brand-dot"></span>
      <span class="brand-name">PANHEARTH</span>
    </div>
    <div class="front-divider"></div>
    <div class="front-details">
      <h1 class="person-name">Marcus Bell</h1>
      <p class="address">57 Larkin Street<br>Marlow Heights<br>QLD 4127 Australia</p>
      <ul class="contact-list">
        <li class="contact-item">
          <svg class="contact-icon" viewBox="0 0 24 24"><path fill="#e8264a" d="M6.6 10.8a15.1 15.1 0 0 0 6.6 6.6l2.2-2.2c.3-.3.7-.4 1-.2 1.1.4 2.3.6 3.6.6.6 0 1 .4 1 1V20c0 .6-.4 1-1 1A17 17 0 0 1 3 4c0-.6.4-1 1-1h3.5c.6 0 1 .4 1 1 0 1.3.2 2.5.6 3.6.1.3 0 .7-.2 1z"/></svg>
          <span>0418563207</span>
        </li>
        <li class="contact-item">
          <svg class="contact-icon" viewBox="0 0 24 24"><path fill="#e8264a" d="M2 5h20v14H2z"/><path fill="none" stroke="#0c0c0c" stroke-width="1.8" d="M2 5l10 8 10-8"/></svg>
          <span>Marcus@PanHearth.com.au</span>
        </li>
        <li class="contact-item">
          <svg class="contact-icon" viewBox="0 0 24 24"><g fill="none" stroke="#e8264a" stroke-width="2"><circle cx="12" cy="12" r="10"/><ellipse cx="12" cy="12" rx="4.5" ry="10"/><path d="M2 12h20M4 7h16M4 17h16"/></g></svg>
          <span>www.<span class="highlight">PanHearth</span>.com.au</span>
        </li>
      </ul>
    </div>
  </section>

  <section class="card card-back">
    <div class="back-lockup">
      <div class="back-mark">
        <span class="brand-dot"></span>
        <span class="brand-name">PANHEARTH</span>
      </div>
      <p class="tagline">Fresh Meals Made To Order</p>
    </div>
  </section>

</main>
</body>
</html>
```